QRV Advisors needs a web site

We need a web site for www.qrvadvisors-example.com. QRV is a mergers and acquisition consulting company that focuses our buyer and seller services on logistics companies. We help put companies together, and help with legal and financial due diligence. We want the web site to express our service and show the logistics components. We want personalized images versus pictures of trucks and airplanes.

Our new logo uses Burgandy and grey colors. Image attached. We are not in to bold, big letters...classy, artistic, low key preferred. Confidentiality, experience, professional are what we want to express on the site.

All we expect for the first part of this project is a home page, and one subpage.  We are budgeting other funds for the technical aspects of the web site

Reason: All that I'm seeing so far is trucks, forklifts and planes. We are a legal mergers and acquisitions firm that focus on logistics. I like some of the images to say logistics, but really want it say legal, financial, and putting companies together. Will pay extra for the sub page if someone can impress us with a home page.

Reason: Swamped with another project at the moment...will work on this over the weekend and provide designer feedback and select final design by Tuesday

```html
<!DOCTYPE html>
<html lang="en">
<head>
<meta charset="utf-8">
<title>QRV Advisors</title>
<link href="https://fonts.googleapis.com/css2?family=Maven+Pro:wght@400;500&display=swap" rel="stylesheet">
<style>
:root{
  --burgundy:#a8123a;
  --burgundy-dark:#8a0d2f;
  --ink:#333;
  --text:#666;
  --hero-bg:#ececec;
  --band:#e6e6e6;
  --footer:#d4d4d4;
  --dark-btn:#3a3a3a;
}
*{box-sizing:border-box;margin:0;padding:0}
html,body{width:918px;height:1200px;overflow:hidden}
body{font-family:"Maven Pro",sans-serif;color:var(--text);background:#fff;position:relative;letter-spacing:.06em}
.abs{position:absolute}
.hero{left:0;top:0;width:918px;height:459px;background:linear-gradient(180deg,#f1f1f1,#e4e4e4)}
.brand-panel{left:52px;top:32px;width:240px;height:104px;background:linear-gradient(180deg,#f7f7f7,#d9d9d9);clip-path:polygon(0 0,100% 0,80% 100%,0 100%);box-shadow:0 2px 4px rgba(0,0,0,.2)}
.brand{left:62px;top:64px;display:flex;align-items:center;gap:10px}
.brand-mark{width:14px;height:14px;background:var(--burgundy)}
.brand-name{font-size:17px;color:var(--burgundy);font-weight:500;letter-spacing:.08em}
.nav{left:248px;top:38px;width:629px;height:92px;background:linear-gradient(180deg,#b5163f,#8f0e31);clip-path:polygon(6% 0,100% 0,100% 100%,0 100%);display:flex;padding-left:45px}
.nav a{color:#fff;text-decoration:none;font-size:12.5px;display:flex;flex-direction:column;align-items:center;justify-content:flex-end;padding:0 18px 12px;gap:12px}
.nav a.active{background:rgba(0,0,0,.18);width:74px;padding:0 0 12px}
.nav svg{width:28px;height:28px;fill:#fff}
.photo{left:65px;top:178px;width:374px;height:249px;border:4px solid #fff;box-shadow:0 2px 6px rgba(0,0,0,.3);background:linear-gradient(135deg,#8a5a3a,#c9a27a 40%,#4b6fa8 60%,#d7c6a8)}
.intro{left:484px;top:184px;width:380px}
.intro h1{font-weight:400;font-size:20px;color:#444;letter-spacing:.08em;margin-bottom:10px}
.intro p{font-size:12.3px;line-height:19.8px;color:#555}
.btn{display:inline-flex;align-items:center;gap:10px;height:32px;padding:0 22px;color:#fff;font-size:12px;margin-top:15px}
.btn-red{background:var(--burgundy)}
.btn-dark{background:var(--dark-btn);margin-left:8px}
.card{top:502px;width:175px}
.card-img{height:116px;border-top:4px solid var(--burgundy);box-shadow:0 0 0 1px #ccc}
.card h3{font-weight:400;font-size:13.5px;color:var(--burgundy);margin:12px 2px 8px}
.card p{font-size:11px;line-height:14.5px;margin:0 2px}
.card ul{list-style:none;margin:8px 2px 0}
.card li{font-size:11px;line-height:17px;display:flex;align-items:center;gap:6px}
.card li svg{width:10px;height:10px}
.more{display:inline-block;margin:10px 2px 0;background:var(--burgundy);color:#fff;font-size:9.5px;padding:6px 17px;box-shadow:2px 2px 2px rgba(0,0,0,.2)}
.quote{left:657px;top:502px;width:196px;height:219px;background:#ebebeb;border:1px solid #d4d4d4}
.quote h2{background:var(--burgundy);color:#fff;font-weight:400;font-size:14px;padding:8px 11px;height:33px}
.field{margin:13px 10px 0;height:26px;background:#fff;border:1px solid #ccc;font-size:9.5px;color:#777;padding:6px 7px}
.field.msg{height:62px;margin-top:8px}
.field.tight{margin-top:8px}
.send{margin:8px 16px 0;height:25px;background:linear-gradient(#555,#2e2e2e);color:#fff;font-size:9.5px;text-align:center;line-height:25px}
.partners{left:0;top:845px;width:918px;height:77px;background:var(--band);display:flex;align-items:center;justify-content:space-around;padding:0 40px}
.partner{font-size:14px;color:#666}
.partner.home{color:var(--burgundy);font-size:17px;font-weight:500}
.badge{width:46px;height:46px;border-radius:50%;background:#9a9a9a}
.footer{left:0;top:922px;width:918px;height:243px;background:var(--footer)}
.col{top:966px}
.col h4{font-weight:400;font-size:13px;color:var(--burgundy);margin-bottom:24px}
.col li{list-style:none;font-size:11px;color:#555;line-height:22.5px;padding-left:3px}
.contact-row{display:flex;gap:8px;font-size:11px;color:#555;line-height:14.5px;margin-bottom:14px}
.contact-row svg{width:14px;height:14px;flex:none;fill:var(--burgundy)}
.bottom{left:0;top:1165px;width:918px;height:35px;background:var(--burgundy);color:#fff;font-size:11px;display:flex;align-items:center;justify-content:space-between;padding:0 40px 0 74px}
.social{display:flex;gap:8px}
.social span{width:19px;height:19px;border-radius:50%;background:#fff}
</style>
</head>
<body>
<section class="hero abs"></section>

<header>
  <div class="brand-panel abs"></div>
  <div class="brand abs"><span class="brand-mark"></span><span class="brand-name">QRV ADVISORS</span></div>
  <nav class="nav abs">
    <a class="active" href="#"><svg viewBox="0 0 24 24"><path d="M12 3 2 12h3v9h5v-6h4v6h5v-9h3z"/></svg>HOME</a>
    <a href="#"><svg viewBox="0 0 24 24"><circle cx="7" cy="8" r="3"/><circle cx="17" cy="8" r="3"/><circle cx="12" cy="10" r="3.5"/><path d="M2 20c0-4 2-6 5-6s3 1 3 1-2 2-2 5zM22 20c0-4-2-6-5-6s-3 1-3 1 2 2 2 5zM7 21c0-4 2-7 5-7s5 3 5 7z"/></svg>ABOUT US</a>
    <a href="#"><svg viewBox="0 0 24 24"><path d="M4 8h5V6a2 2 0 1 1 4 0v2h5v5h-2a2 2 0 1 0 0 4h2v4H4z"/></svg>OUR SERVICES ▾</a>
    <a href="#"><svg viewBox="0 0 24 24"><circle cx="12" cy="7" r="4"/><path d="M4 22c0-5 3-9 8-9s8 4 8 9z"/></svg>OUR CLIENTS</a>
    <a href="#"><svg viewBox="0 0 24 24"><path d="M2 5h20v14H2zM2 5l10 8 10-8" stroke="#a8123a" stroke-width="1.5"/></svg>CONTACT US</a>
  </nav>
</header>

<div class="photo abs" role="img" aria-label="Professional reviewing a tablet in a warehouse aisle"></div>
<div class="intro abs">
  <h1>QRV ADVISORS</h1>
  <p>QRV assists business owners within the logistics industry to implement growth and exit strategies. We offer business planning and merger and acquisition(M&amp;A) advisory services. QRV services are offered by industry executives with extensive M&amp;A experience.&nbsp; Your company will benefit from a unique and outside perspective from consultants that understand your business.</p>
  <span class="btn btn-red">Read more <svg width="9" height="9" viewBox="0 0 10 10"><path d="M1 1l8 4-8 4z" fill="#fff"/></svg></span><span class="btn btn-dark">Contact us <svg width="12" height="9" viewBox="0 0 12 9"><rect width="12" height="9" fill="#fff"/><path d="M0 0l6 5 6-5" stroke="#3a3a3a" fill="none"/></svg></span>
</div>

<article class="card abs" style="left:58px">
  <div class="card-img" role="img" aria-label="Hand moving a chess piece" style="background:linear-gradient(160deg,#eee,#cfcfcf 60%,#888)"></div>
  <h3>Growth and Exit strategies</h3>
  <p>Lorem ipsum dolor sit amet, consectetur adipiscing elit. Etiam facilisis pulvinar gravida. Phasellus et sagittis quam.</p>
  <ul>
    <li><svg viewBox="0 0 10 10"><circle cx="5" cy="5" r="5" fill="#a8123a"/><path d="M2.5 5l2 2 3-4" stroke="#fff" fill="none"/></svg>Adipiscing elit</li>
    <li><svg viewBox="0 0 10 10"><circle cx="5" cy="5" r="5" fill="#a8123a"/><path d="M2.5 5l2 2 3-4" stroke="#fff" fill="none"/></svg>Consecteturr gravida sagittis</li>
    <li><svg viewBox="0 0 10 10"><circle cx="5" cy="5" r="5" fill="#a8123a"/><path d="M2.5 5l2 2 3-4" stroke="#fff" fill="none"/></svg>Phasellus et sagittis lorem</li>
  </ul>
  <span class="more">more details</span>
</article>

<article class="card abs" style="left:257px">
  <div class="card-img" role="img" aria-label="Business people shaking hands in an office" style="background:linear-gradient(135deg,#dfe3e6,#f4f4f4 50%,#b9c0c6)"></div>
  <h3>Merger &amp; Acquisition</h3>
  <p>Lorem ipsum dolor sit amet, consectetur adipiscing elit. Etiam facilisis pulvinar gravida. Phasellus et sagittis quam. Donec tincidunt nulla urna, consectetur adipiscing elit.</p>
  <span class="more">more details</span>
</article>

<article class="card abs" style="left:456px">
  <div class="card-img" role="img" aria-label="Hands typing on a laptop beside documents" style="background:linear-gradient(135deg,#e9e9e9,#bcbcbc 50%,#2d3a5a)"></div>
  <h3>Business Planning</h3>
  <p>Lorem ipsum dolor sit amet, consectetur adipiscing elit. Etiam facilisis pulvinar gravida. Phasellus et sagittis quam. Donec tincidunt nulla urna.</p>
  <ul>
    <li><svg viewBox="0 0 10 10"><circle cx="5" cy="5" r="5" fill="#a8123a"/><path d="M2.5 5l2 2 3-4" stroke="#fff" fill="none"/></svg>Adipiscing elit</li>
    <li><svg viewBox="0 0 10 10"><circle cx="5" cy="5" r="5" fill="#a8123a"/><path d="M2.5 5l2 2 3-4" stroke="#fff" fill="none"/></svg>Consecteturr gravida sagittis</li>
  </ul>
  <span class="more">more details</span>
</article>

<aside class="quote abs">
  <h2>Get a Free Quote</h2>
  <div class="field">Firstname</div>
  <div class="field tight">Email</div>
  <div class="field msg">Message</div>
  <div class="send">SEND MESSAGE</div>
</aside>

<section class="partners abs">
  <span class="partner">NORTHGATE</span>
  <span class="partner">HARBOR CREST</span>
  <span class="badge"></span>
  <span class="partner">MERIDIAN</span>
  <span class="partner">ALDER &amp; FINCH</span>
  <span class="partner home">QRV ADVISORS</span>
</section>

<footer class="footer abs"></footer>
<div class="col abs" style="left:97px">
  <h4>ABOUT US</h4>
  <ul><li>Who we are</li><li>Client List</li><li>Contact Info</li></ul>
</div>
<div class="col abs" style="left:243px">
  <h4>SERVICES OFFERED</h4>
  <ul><li>Growth &amp; Exit Strategies</li><li>Business Planning</li><li>Merger &amp; Aquisition</li><li>Management System</li></ul>
</div>
<div class="col abs" style="left:469px">
  <h4>ADDITIONAL INFO</h4>
  <ul><li>Sitemap</li><li>FAQ</li><li>Privacy Policy</li><li>Terms &amp; Agreement</li></ul>
</div>
<div class="col abs" style="left:667px">
  <h4>CONTACT INFO</h4>
  <div class="contact-row"><svg viewBox="0 0 24 24"><path d="M12 2a7 7 0 0 0-7 7c0 5 7 13 7 13s7-8 7-13a7 7 0 0 0-7-7zm0 10a3 3 0 1 1 0-6 3 3 0 0 1 0 6z"/></svg><span>Lorem Ipsum Address<br>1200 Example Parkway<br>Springfield, ST<br>00000</span></div>
  <div class="contact-row"><svg viewBox="0 0 24 24"><path d="M3 9c0-3 18-3 18 0v2h-5V9H8v2H3zM6 12h12l2 8H4z"/></svg><span>(555) 010-2417</span></div>
  <div class="contact-row"><svg viewBox="0 0 24 24"><path d="M2 6h20v12H2z"/><path d="M2 6l10 7 10-7" stroke="#d4d4d4" fill="none"/></svg><span>hello@qrvadvisors-example.com</span></div>
</div>

<div class="bottom abs">
  <span>QRV Advisors All Rights Reserved © 2014</span>
  <span class="social"><span></span><span></span><span></span></span>
</div>
</body>
</html>
```